Maple Beacon Website

We are starting a marketing company and to do that we need a website! We want a website that will inspire and persuade to bring out the awesomeness in our clients.
What we want to see:
- Inspirational and persuasive imagery that relate to Branding.
- No cliche images eg. business man, suits and hand shakes
- We want to transform and educate our clients.
- We want to show them the path and would like our website to really act as a guide that guides them step by step through our process.
- We want the portray that we are an investment but not have a pretentious way to it. We put our heart into every project and that is how we treat our clients.
-When you submit your design please include what platform you have created for. Preference would be Wordpress or Joobla.

We have included the psd file for the wire frame, logo files, font files, site map and a link to a video we create to give you more information on what we would like to see. http://clipvault.example/t/qk82LmZpr

Feel free to make small modification to the logos if you think it will improve it. Your creativity and advice is most welcome.
Updates

One thing we forgot. We would like to have our contact information near the top of the website as well as at the bottom.  Here is out contact info:

Email: info@maplebeacon.example
Phone: 587-555-0142

Project Deadline Extended
Reason: As we are new with the platform and that we want to optimize our results, we decided to extend the deadline by 15 days. Thanks!

Target Market(s)

28-60, Male and Female, Oil field, Local Businesses, Dentists, Chiropractors, Hair salon, Construction/Renovation, Events etc

Industry/Entity Type

Investment

Requirements
Must have
• - 4 Inspirational and persuasive Imagery for the top portion of the website
- Must have a feel as if your not on a website an example of this is linked below.
http://www.artbidhub.example/design/402957/web-design-by-lena-torvik
Nice to have
• - Creative advice from you.
- Creative buttons for Get Free Quote and Subscribe buttons. Something out of the box that draws peoples attention. eg. a 'B' button. Just and example but still something related to branding.
Should not have
• No Cliches

```html
<!DOCTYPE html>
<html lang="en">
<head>
<meta charset="utf-8">
<title>Maple Beacon</title>
<link rel="stylesheet" href="https://fonts.googleapis.com/css2?family=Ubuntu:wght@500;700&family=Arimo:wght@400;700&display=swap">
<style>
  :root {
    --green: #8aab3c;
    --green-dark: #6f8f22;
    --green-text: #7f9f1e;
    --ink: #333333;
    --body-text: #666666;
    --page: #efefef;
    --header-top: #e6e6e6;
    --header-bottom: #c9c9c9;
    --rule: #bdbdbd;
    --footer: #1b1b1b;
    --social: #a9a9a9;
  }
  * { box-sizing: border-box; margin: 0; padding: 0; }
  html, body { width: 1200px; height: 718px; overflow: hidden; }
  body { background: var(--page); font-family: "Arimo", Arial, sans-serif; position: relative; }

  .top-strip { position: absolute; left: 0; top: 0; width: 1200px; height: 9px; background: var(--green); }
  .header { position: absolute; left: 0; top: 9px; width: 1200px; height: 350px;
    background: linear-gradient(var(--header-top), var(--header-bottom)); }

  .sidebar { position: absolute; left: 150px; top: 9px; width: 225px; height: 300px; }
  .brand { position: absolute; left: 12px; top: 20px; display: flex; align-items: center; gap: 8px; }
  .brand-dot { width: 16px; height: 16px; border-radius: 50%; background: var(--green); }
  .brand-name { font-family: "Ubuntu", sans-serif; font-weight: 700; font-size: 26px; color: #6e6e6e; letter-spacing: .5px; }
  .tagline { position: absolute; left: 38px; top: 75px; font-family: "Ubuntu", sans-serif; font-weight: 500;
    font-size: 13px; color: #666; font-style: italic; }

  .nav { position: absolute; left: 0; top: 111px; width: 225px; list-style: none; }
  .nav li { height: 37.6px; border-top: 1px solid var(--rule); box-shadow: inset 0 1px 0 #f2f2f2;
    display: flex; align-items: center; padding-left: 42px; position: relative;
    font-size: 12.5px; color: var(--ink); letter-spacing: .6px; }
  .nav li::before { content: ""; position: absolute; left: 18px; top: 50%; margin-top: -3px;
    border-left: 4px solid #aaa; border-top: 3px solid transparent; border-bottom: 3px solid transparent; }

  .hero { position: absolute; left: 375px; top: 9px; width: 675px; height: 300px;
    background: radial-gradient(circle at 72% 40%, #f4fbe9 0%, #dff1c8 22%, #b9e07a 55%, #8fc443 100%); }
  .hero-title { position: absolute; left: 36px; top: 126px; font-family: "Ubuntu", sans-serif; font-weight: 700;
    font-size: 38px; color: var(--ink); letter-spacing: -.5px; }
  .pager { position: absolute; right: 3px; bottom: 3px; display: flex; gap: 3px; }
  .pager span { width: 15px; height: 15px; background: #000; color: #fff; font-size: 9px; font-weight: 700;
    display: flex; align-items: center; justify-content: center; }
  .pager .active { background: var(--green); }

  .connect-bar { position: absolute; left: 150px; top: 309px; width: 900px; height: 50px;
    border-top: 1px solid var(--rule); display: flex; align-items: center; }
  .connect-label { font-family: "Ubuntu", sans-serif; font-weight: 700; font-size: 14px; line-height: 14px;
    color: var(--green); margin-left: 6px; width: 70px; }
  .social { display: flex; gap: 4px; margin-left: 4px; }
  .social span { width: 26px; height: 26px; border-radius: 50%; background: var(--social); }
  .newsletter { font-family: "Ubuntu", sans-serif; font-weight: 700; font-size: 18px; color: var(--ink);
    margin-left: 14px; letter-spacing: .1px; }
  .btn { height: 34px; border-radius: 3px; color: #fff; font-family: "Arimo", sans-serif; font-weight: 700;
    font-size: 15px; display: flex; align-items: center; justify-content: center;
    background: linear-gradient(#8cae3a, var(--green-dark)); border: 1px solid #5d7a1a; }
  .btn-subscribe { width: 93px; margin-left: 6px; }
  .btn-quote { width: 131px; margin-left: 5px; }

  .welcome { position: absolute; left: 0; top: 377px; width: 1200px; text-align: center;
    font-family: "Ubuntu", sans-serif; font-weight: 700; font-size: 21px; color: var(--green-text); }
  .intro { position: absolute; left: 300px; top: 425px; width: 602px; font-size: 13.1px; line-height: 17px;
    color: var(--body-text); text-align: justify; }
  .intro p + p { margin-top: 17px; }

  .footer { position: absolute; left: 0; top: 626px; width: 1200px; height: 92px; background: var(--footer);
    border-top: 1px solid #333; }
  .footer-links { position: absolute; left: 0; top: 19px; width: 1200px; text-align: center;
    font-size: 12.5px; color: var(--green); }
  .footer-links .sep { margin: 0 9px; }
  .copyright { position: absolute; left: 0; top: 51px; width: 1200px; text-align: center;
    font-size: 13px; color: #8a8a8a; letter-spacing: .3px; }
</style>
</head>
<body>
  <div class="top-strip"></div>
  <header class="header"></header>

  <aside class="sidebar">
    <div class="brand"><span class="brand-dot"></span><span class="brand-name">MAPLE BEACON</span></div>
    <div class="tagline">Because You´re Awesome!</div>
    <ul class="nav">
      <li>STRATEGY</li>
      <li>PORTFOLIO</li>
      <li>ABOUT US</li>
      <li>CONTACT US</li>
      <li>BLOG</li>
    </ul>
  </aside>

  <section class="hero" role="img" aria-label="Sunlit green leaves with a glass globe glowing against a bright sky">
    <div class="hero-title">Maple Beacon</div>
    <div class="pager"><span class="active">1</span><span>2</span><span>3</span><span>4</span></div>
  </section>

  <div class="connect-bar">
    <div class="connect-label">Connect<br>with us !</div>
    <div class="social">
      <span aria-label="Social network 1"></span><span aria-label="Social network 2"></span>
      <span aria-label="Social network 3"></span><span aria-label="Video channel"></span>
      <span aria-label="RSS feed"></span>
    </div>
    <div class="newsletter">Get Tips and Tricks! Subscribe to our Newsletter.</div>
    <div class="btn btn-subscribe">Subscribe</div>
    <div class="btn btn-quote">Get a Free Quote</div>
  </div>

  <h1 class="welcome">WELCOME!</h1>
  <div class="intro">
    <p>Lorem ipsum dolor sit amet, consectetur adipisicing elit, sed do eiusmod tempor incididunt ut labore et dolore magna aliqua. Ut enim ad minim veniam, quis nostrud exercitation ullamco laboris nisi ut aliquip ex ea commodo consequat. Duis aute irure dolor in reprehenderit in voluptate velit esse cillum dolore eu fugiat nulla pariatur. Excepteur sint occaecat cupidatat non proident, sunt in culpa qui officia deseruntilil</p>
    <p>Sed ut perspiciatis unde omnis iste natus error sit voluptatem accusantium doloremque laudantium, totam rem aperiam, eaque ipsa quae ab illo inventore veritatis et quasi architecto beatae vitae dicta sunt explicabo. Nemo enim ipsam voluptatem quia voluptas sit aspernatur aut odit aut fugit, sed quia conse­quuntur magni dolores eos qui ratione voluptatem sequi nesciunt. Neque porro quisquam est, qui dolom</p>
  </div>

  <footer class="footer">
    <div class="footer-links">Site Map<span class="sep">|</span>Strategy<span class="sep">|</span>Portfolio<span class="sep">|</span>About Us<span class="sep">|</span>Contact Us<span class="sep">|</span>Blog</div>
    <div class="copyright">© MAPLE BEACON INC. 2013</div>
  </footer>
</body>
</html>
```